Patent Law

Need to develop a home page for a patent lawyer.

Colors should go with logo, blues...

Company Name- Velun Tresk, PLLC

Company Overview-

I am an Intellectual Property Lawyer and focus on patents, copyrights, trademarks, & trade secrets. I work with small businesses and start ups in the chemical and biotech industries.

Why Us-

I am small firm that can provide large-firm service at a reasonable price. I also can charge flat-fees for entreprenuers in certain practice areas.

Services-
Intellectual Property
Patents
Copyrights
Trademarks
Trade secrets
Healthcare Compliance
Elder law
Wills
Trusts

Website we like-
http://www.quorvantlegal.example/ - within industry!!
http://www.daltrowemiko.example/
http://ulbrixtane.example/
http://thegravelcounsel.example/

Target Market(s)

My customers will be small business, specifically small start-up companies in the chemical and biotech arena.

Industry/Entity Type

Trade

Requirements
Must have
• Colors should go with logo, blues...

```html
<!DOCTYPE html>
<html lang="en">
<head>
<meta charset="utf-8">
<title>Velun Tresk, PLLC — Intellectual Property Law</title>
<link href="https://fonts.googleapis.com/css2?family=Open+Sans:wght@400;600;700&family=Playfair+Display:wght@400;700&display=swap" rel="stylesheet">
<style>
:root{
  --blue:#1f8fd6;
  --blue-dark:#0f5f9e;
  --blue-light:#4fb3ee;
  --nav:#2a8ed4;
  --orange:#f39a1e;
  --page:#e6e7e9;
  --footer:#3a3b3d;
  --footer-dark:#2b2c2e;
  --text:#4a4a4a;
  --white:#ffffff;
}
*{box-sizing:border-box;margin:0;padding:0}
html,body{width:705px;height:1200px;overflow:hidden}
body{background:var(--page);font-family:"Open Sans",Arial,sans-serif;color:var(--text);position:relative}

.site-header{position:absolute;left:0;top:0;width:705px;height:92px;background:linear-gradient(#fbfbfb,#e4e5e7)}
.brand{position:absolute;left:40px;top:28px;display:flex;align-items:center;gap:8px}
.brand-dot{width:26px;height:26px;border-radius:50%;background:var(--blue-dark)}
.brand-name{font-size:13px;font-weight:600;color:var(--blue-dark);letter-spacing:.3px}
.search{position:absolute;left:532px;top:16px;width:140px;height:20px;border:1px solid #c9cbce;border-radius:10px;background:#fff;font-size:9px;color:#999;padding:3px 10px}
.search-btn{position:absolute;right:3px;top:2px;width:14px;height:14px;border-radius:50%;background:var(--blue)}
.social{position:absolute;left:582px;top:40px;display:flex;gap:5px}
.social span{width:17px;height:17px;border-radius:3px;background:var(--blue)}
.social span:nth-child(2){background:var(--blue-dark)}
.social span:nth-child(4){background:var(--orange)}

.main-nav{position:absolute;left:0;top:94px;width:705px;height:24px;background:linear-gradient(var(--blue-light),var(--nav))}
.main-nav ul{list-style:none;display:flex;gap:36px;padding-left:44px;height:100%;align-items:center}
.main-nav li{font-size:10px;color:var(--white);letter-spacing:.6px}

.hero{position:absolute;left:33px;top:130px;width:640px;height:296px;border-radius:4px;overflow:hidden;background:var(--white);padding:4px}
.hero-photo{width:100%;height:100%;border-radius:3px;background:linear-gradient(180deg,#3a2414 0%,#6b4426 45%,#a27a52 72%,#e6dccd 100%)}
.hero-badge{position:absolute;left:445px;top:22px;width:162px;height:162px;border-radius:50%;background:radial-gradient(circle at 40% 35%,#3aa6ea,#1467ad);border:3px solid rgba(255,255,255,.35);display:flex;flex-direction:column;align-items:center;justify-content:center;color:#fff;text-align:center}
.hero-badge small{font-size:11px;letter-spacing:1.5px}
.hero-badge strong{font-family:"Playfair Display",Georgia,serif;font-size:13px;font-weight:400;letter-spacing:.6px;margin-top:4px;white-space:nowrap}
.hero-dots{position:absolute;left:14px;top:268px;display:flex;gap:5px}
.hero-dots i{width:9px;height:9px;border-radius:50%;background:#fff;border:1px solid #ccc}
.hero-dots i:last-child{background:var(--blue)}

.overview{position:absolute;left:33px;top:438px;width:640px;height:176px;border-radius:3px;background:linear-gradient(100deg,#0f5c9c 0%,#1f8fd6 55%,#47acea 100%);color:#fff}
.overview-portrait{position:absolute;left:22px;top:25px;width:124px;height:124px;border-radius:50%;border:4px solid #fff;background:linear-gradient(#8a5a40,#4a2c20)}
.overview h2{position:absolute;left:168px;top:32px;font-size:18px;font-weight:400}
.overview p{position:absolute;left:168px;top:64px;width:440px;font-size:11px;line-height:15px}
.btn-orange{position:absolute;left:240px;top:116px;width:108px;height:24px;border-radius:3px;background:linear-gradient(#f7ad3d,#e98710);color:#fff;font-size:9.5px;text-align:center;line-height:24px;letter-spacing:.5px}

.services{position:absolute;left:33px;top:624px;width:640px;height:282px;background:linear-gradient(#d9dadc,#c9cbcd);border-radius:3px}
.slide-arrow{position:absolute;top:108px;width:18px;height:74px;background:var(--blue);border-radius:3px}
.slide-arrow.left{left:-8px}
.slide-arrow.right{right:-8px}
.service{position:absolute;top:22px;width:150px;text-align:center}
.service-img{width:150px;height:150px;border-radius:50%;border:5px solid var(--blue);box-shadow:0 0 0 3px #fff}
.service-copyrights .service-img{background:radial-gradient(#6ab6e8,#0e3e78)}
.service-trusts .service-img{background:radial-gradient(#e8e8e8,#3d3d3d)}
.service-trademarks .service-img{background:radial-gradient(#f4f4f4,#b5303a)}
.service h3{font-size:9.5px;font-weight:700;color:var(--blue-dark);margin-top:10px;letter-spacing:.4px}
.service p{font-size:8px;line-height:11px;color:#666;margin-top:4px}
.btn-blue{display:inline-block;margin-top:8px;width:60px;height:17px;background:var(--blue);color:#fff;font-size:7.5px;line-height:17px;border-radius:2px}

.site-footer{position:absolute;left:0;top:928px;width:705px;height:254px;background:linear-gradient(var(--footer),var(--footer-dark))}
.footer-title{position:absolute;font-size:12px;font-weight:400;color:#fff;letter-spacing:.6px;top:18px}
.news-item{position:absolute;left:58px;width:200px;display:flex;gap:8px}
.news-thumb{flex:none;width:56px;height:50px;background:linear-gradient(#e3e3e3,#8d8d8d);border:2px solid #fff}
.news-text{width:130px}
.news-text h5{font-size:9.5px;line-height:12px;color:#fff;font-weight:600}
.news-text p{font-size:8px;line-height:11px;color:#aaa;margin-top:2px}
.view-all{position:absolute;left:58px;top:200px;font-size:8px;color:#ddd;letter-spacing:.4px}
.quicklinks{position:absolute;left:340px;top:60px;list-style:none}
.quicklinks li{font-size:10px;color:#ddd;margin-bottom:9px}
.quicklinks li::before{content:"› ";color:var(--blue-light)}
.location{position:absolute;left:518px;top:58px;font-size:9.5px;color:#ddd;line-height:13px}
.location .row{display:flex;gap:8px;margin-bottom:9px}
.location svg{flex:none;margin-top:1px}
.footer-social{display:flex;gap:5px;margin-top:4px}
.footer-social span{width:17px;height:17px;border-radius:3px;background:var(--blue)}
.footer-social span:nth-child(4){background:var(--orange)}

.bottom-bar{position:absolute;left:0;top:1182px;width:705px;height:18px;background:#e9eaeb;font-size:7.5px;color:#666;line-height:18px}
.bottom-bar .copy{position:absolute;left:44px}
.bottom-bar .links{position:absolute;right:44px}
</style>
</head>
<body>

<header class="site-header">
  <div class="brand"><span class="brand-dot"></span><span class="brand-name">VELUN TRESK, PLLC</span></div>
  <div class="search">Search<span class="search-btn"></span></div>
  <div class="social"><span></span><span></span><span></span><span></span></div>
</header>

<nav class="main-nav">
  <ul><li>HOME</li><li>ABOUT US</li><li>SERVICES</li><li>LATEST NEWS</li><li>CONTACT US</li></ul>
</nav>

<section class="hero">
  <div class="hero-photo" role="img" aria-label="Law library with an open book and a laptop on a desk"></div>
  <div class="hero-badge"><small>WELCOME TO</small><strong>VELUN TRESK, PLLC</strong></div>
  <div class="hero-dots"><i></i><i></i><i></i></div>
</section>

<section class="overview">
  <div class="overview-portrait" role="img" aria-label="Portrait of the attorney"></div>
  <h2>Company Overview</h2>
  <p>I am an Intellectual Property Lawyer and focus on patents, copyrights, trademarks, &amp; trade secrets. I work with small businesses and start ups in the chemical and biotech industries.</p>
  <div class="btn-orange">READ MORE</div>
</section>

<section class="services">
  <div class="slide-arrow left"></div>
  <div class="service service-copyrights" style="left:52px">
    <div class="service-img" role="img" aria-label="Copyright symbol on a digital blue background"></div>
    <h3>COPYRIGHTS</h3>
    <p>Lorem ipsum dolor sit amet, consectetur adipiscing elit. Curabitur pretium risus at nibh euismod tempor.</p>
    <span class="btn-blue">READ MORE</span>
  </div>
  <div class="service service-trusts" style="left:245px">
    <div class="service-img" role="img" aria-label="Business handshake in black and white"></div>
    <h3>TRUSTS</h3>
    <p>Lorem ipsum dolor sit amet, consectetur adipiscing elit. Curabitur pretium risus at nibh euismod tempor.</p>
    <span class="btn-blue">READ MORE</span>
  </div>
  <div class="service service-trademarks" style="left:438px">
    <div class="service-img" role="img" aria-label="Registered trademark symbol in red and white"></div>
    <h3>TRADEMARKS</h3>
    <p>Lorem ipsum dolor sit amet, consectetur adipiscing elit. Curabitur pretium risus at nibh euismod tempor.</p>
    <span class="btn-blue">READ MORE</span>
  </div>
  <div class="slide-arrow right"></div>
</section>

<footer class="site-footer">
  <h4 class="footer-title" style="left:58px">LATEST NEWS</h4>
  <div class="news-item" style="top:60px">
    <div class="news-thumb" role="img" aria-label="Presenter at a whiteboard"></div>
    <div class="news-text">
      <h5>News title goes here here</h5>
      <p>Lorem ipsum dolor sit amet, consectetur adipiscing elit.</p>
    </div>
  </div>
  <div class="news-item" style="top:124px">
    <div class="news-thumb" role="img" aria-label="Presenter at a whiteboard"></div>
    <div class="news-text">
      <h5>News title goes here here</h5>
      <p>Lorem ipsum dolor sit amet, consectetur adipiscing elit.</p>
    </div>
  </div>
  <div class="view-all">VIEW ALL NEWS</div>

  <h4 class="footer-title" style="left:332px">QUICKLINKS</h4>
  <ul class="quicklinks"><li>Home</li><li>About us</li><li>Services</li><li>Latest News</li><li>Contact us</li></ul>

  <h4 class="footer-title" style="left:518px">LOCATION</h4>
  <div class="location">
    <div class="row">
      <svg width="10" height="10" viewBox="0 0 10 10"><path d="M1 5 5 1 9 5V9H1Z" fill="#ddd"/></svg>
      <span>1344 Your Address<br>Location here, NY<br>Country name</span>
    </div>
    <div class="row">
      <svg width="10" height="10" viewBox="0 0 10 10"><path d="M2 1h2l1 2-1.2 1a5 5 0 0 0 2.2 2.2L7 5l2 1v2a1 1 0 0 1-1 1A7 7 0 0 1 1 2a1 1 0 0 1 1-1Z" fill="#ddd"/></svg>
      <span>(02) 1234-5678<br>(02) 1234-5678</span>
    </div>
    <div class="row">
      <svg width="10" height="10" viewBox="0 0 10 10"><rect x="0.5" y="2" width="9" height="6" fill="#ddd"/><path d="M.5 2 5 5.5 9.5 2" stroke="#3a3b3d" fill="none"/></svg>
      <span>your@email.com</span>
    </div>
    <div class="footer-social"><span></span><span></span><span></span><span></span></div>
  </div>
</footer>

<div class="bottom-bar">
  <span class="copy">Copyright 2013 · All rights reserved</span>
  <span class="links">Sitemap &nbsp;|&nbsp; FAQ &nbsp;|&nbsp; Privacy Policy</span>
</div>

</body>
</html>
```